Business Card Design Project

We are not a new company, but renamed to "Vantorin Kitchens" last year. We specialize in modern high-end cabinetry imports. We would like to communicate a sense of quality and cutting edge technology. Ideally the design would incorporate our logo colors, silver, red and preferably a black, matte background. Though we are open to suggestions.
Logo is attached.
Edit: I have attached rough drafts of the previous cards, this way you will have all necessary content that needs to go on the cards.
Updates
Project Deadline Extended
Reason: We have received a lot of great designs, but due to the sheer number we couldn't respond to all. We will extend the deadline for another 7 days to finalize and provide feedback to designers.
Thank you for your hard work!
Industry/Entity Type
Business
Look and feel
Each slider illustrates characteristics of the customer's brand and the style your logo design should communicate.

```html
<!DOCTYPE html>
<html lang="en">
<head>
<meta charset="utf-8">
<title>Vantorin Kitchens – Business Cards</title>
<link href="https://fonts.googleapis.com/css2?family=Arimo:wght@400;700&display=swap" rel="stylesheet">
<style>
  :root {
    --stage: #e8e5e0;
    --label: #2a2622;
    --card-dark: #141516;
    --card-mid: #2b2c2e;
    --silver: #c9c9c9;
    --text: #f2f2f2;
    --divider: #55575a;
    --accent: #c4161c;
    --dots-dark: #0c0c0c;
    --dots-light: #5a5a5a;
  }
  * { margin: 0; padding: 0; box-sizing: border-box; }
  html, body { width: 1200px; height: 788px; overflow: hidden; }
  body {
    position: relative;
    background: var(--stage);
    font-family: "Arimo", Arial, sans-serif;
  }
  .sheet-label {
    position: absolute;
    width: 200px;
    margin-left: -100px;
    text-align: center;
    font-size: 21px;
    color: var(--label);
  }
  .card {
    position: absolute;
    width: 525px;
    height: 299px;
    border-radius: 22px;
    overflow: hidden;
    color: var(--text);
    background:
      radial-gradient(ellipse 70% 60% at 40% 30%, rgba(255,255,255,0.07), transparent 70%),
      linear-gradient(160deg, var(--card-mid), var(--card-dark));
  }
  .card--solid { background: linear-gradient(170deg, #101010, #050505); }
  .card-front { top: 71px; }
  .card-back { top: 447px; }

  .brand {
    position: absolute;
    display: flex;
    align-items: center;
    gap: 10px;
    color: var(--silver);
    font-weight: 700;
    letter-spacing: 1px;
    text-transform: uppercase;
    white-space: nowrap;
  }
  .brand-mark { display: block; background: var(--accent); }
  .brand--small { left: 30px; top: 100px; font-size: 20px; }
  .brand--small .brand-mark { width: 12px; height: 12px; }
  .brand--large {
    left: 0; right: 0; top: 160px;
    justify-content: center;
    font-size: 30px;
  }
  .brand--large .brand-mark { width: 18px; height: 18px; }

  .divider {
    position: absolute;
    left: 298px; top: 88px;
    width: 1px; height: 42px;
    background: var(--divider);
  }
  .person { position: absolute; left: 316px; top: 90px; }
  .person-name { font-size: 18px; line-height: 21px; }
  .person-name--bold { font-weight: 700; }
  .person-role { font-size: 14px; line-height: 19px; }
  .contact {
    position: absolute;
    left: 316px; top: 190px;
    font-size: 13px;
    line-height: 21px;
  }
  .contact b { font-weight: 700; }
  .contact .email { margin-top: 4px; }
  .address {
    position: absolute;
    left: 34px; top: 240px;
    font-size: 13px;
    line-height: 18px;
  }
  .texture {
    position: absolute;
    background: radial-gradient(ellipse at center, var(--dots-light), var(--dots-dark) 75%, transparent 100%);
    opacity: 0.8;
  }
  .texture--top { left: 0; top: 0; width: 300px; height: 90px; }
  .texture--bottom { right: 0; bottom: 0; width: 260px; height: 90px; }
</style>
</head>
<body>
  <div class="sheet-label" style="left:307px; top:22px;">front</div>
  <div class="sheet-label" style="left:884px; top:22px;">front-1</div>
  <div class="sheet-label" style="left:314px; top:405px;">back</div>
  <div class="sheet-label" style="left:884px; top:405px;">Back - 1</div>

  <section class="card card-front" style="left:53px;">
    <div class="brand brand--small"><span class="brand-mark"></span>Vantorin Kitchens</div>
    <div class="divider"></div>
    <div class="person">
      <div class="person-name person-name--bold">MAREK DOLAN</div>
      <div class="person-role">President</div>
    </div>
    <div class="contact">
      <div><b>phone</b> : 555.210.0147</div>
      <div><b>cell</b> : 555.318.2046</div>
      <div><b>fax</b> : 555.210.0152</div>
      <div class="email">marek@vantorinkitchens.ca</div>
    </div>
    <div class="address">1820 - 47 Ave.<br>Lakeview, AB T0X 2K4</div>
  </section>

  <section class="card card-front" style="left:622px;">
    <div class="brand brand--small"><span class="brand-mark"></span>Vantorin Kitchens</div>
    <div class="divider"></div>
    <div class="person">
      <div class="person-name">ADRIAN DOLAN</div>
      <div class="person-role">Director</div>
    </div>
    <div class="contact">
      <div><b>phone</b> : 555.210.0147</div>
      <div><b>cell</b> : 555.604.7719</div>
      <div><b>fax</b> : 555.210.0152</div>
      <div class="email">adrian@vantorinkitchens.ca</div>
    </div>
    <div class="address">1820 - 47 Ave.<br>Lakeview, AB T0X 2K4</div>
  </section>

  <section class="card card-back" style="left:56px;">
    <div class="brand brand--large"><span class="brand-mark"></span>Vantorin Kitchens</div>
  </section>

  <section class="card card-back card--solid" style="left:624px;">
    <div class="texture texture--top" role="img" aria-label="Perforated metal texture"></div>
    <div class="texture texture--bottom" role="img" aria-label="Perforated metal texture"></div>
    <div class="brand brand--large"><span class="brand-mark"></span>Vantorin Kitchens</div>
  </section>
</body>
</html>
```